Construction material supplies company business card ****

1. Full company name “K T Masonry Works Ltd”
I am after a Business card design for the company as a whole. We are better known in Solomon Islands as “K T Masonry” for short.

We are a building materials supplier of
Ready Mixed Concrete, Bricks and Blocks,
Quarry products- gravel, aggregates, sand etc.
Cement distributor/retailer of reputable brands.
Other prefab concrete products. Culverts, wave breakers, concrete retaining blocks etc.

2. Competitive Advantage over Competition: Quality, efficient, professional, dependable, reliable

3. We want people to feel trust worthy, high quality, strong when they see our brand

5. No preference to color. Maybe more sturdy and corporate. Not fancy.

Industry/Entity Type

CONSTRUCTION SUPPLY

Contact Information for Business Card

Name, Position, office phone mob phone, email

Requirements
Must have
• the company logo
Nice to have
• would like to see a mixture of designs, of with logo only and also with simple graphic designs to bring out the company whilst still have the strong sturdy professional feeling

```html
<!DOCTYPE html>
<html lang="en">
<head>
<meta charset="utf-8">
<title>K T Masonry – Business Card</title>
<link rel="stylesheet" href="https://fonts.googleapis.com/css2?family=Roboto:wght@400;500;700&display=swap">
<style>
  :root {
    --backdrop: #2a2a2a;
    --navy: #2c4a6e;
    --navy-deep: #1d3658;
    --navy-band: rgba(14, 36, 66, 0.72);
    --ink: #1f3d63;
    --paper: #e3e4e5;
    --white: #ffffff;
    --soft-white: #e6ecf3;
  }
  * { box-sizing: border-box; margin: 0; padding: 0; }
  html, body {
    width: 1200px; height: 1138px; overflow: hidden;
    background: var(--backdrop);
    font-family: "Roboto", Arial, sans-serif;
  }
  .card {
    position: absolute;
    border-radius: 16px;
    overflow: hidden;
  }
  /* Front */
  .card-front {
    left: 274px; top: 185px; width: 623px; height: 377px;
    background: linear-gradient(160deg, #3a5a80 0%, var(--navy) 45%, var(--navy-deep) 100%);
    color: var(--white);
    text-align: center;
  }
  .card-front .stripes { position: absolute; inset: 0; }
  .brand-name {
    position: absolute; left: 0; right: 0; top: 70px;
    font-size: 54px; font-weight: 700; letter-spacing: 2px;
    color: var(--white);
  }
  .intro-pill {
    position: absolute; left: 138px; top: 187px; width: 347px; height: 40px;
    border-radius: 20px;
    background: #2a4a72;
    border: 1px solid rgba(255,255,255,0.18);
    font-size: 16px; line-height: 38px;
    color: var(--soft-white);
    z-index: 2;
  }
  .product-band {
    position: absolute; left: 0; right: 0; top: 215px; height: 78px;
    background: var(--navy-band);
    padding-top: 26px;
    font-size: 16px; line-height: 22px;
    color: var(--soft-white);
  }
  .product-more {
    position: absolute; left: 0; right: 0; top: 306px;
    font-size: 16px; line-height: 25px;
    color: var(--soft-white);
  }
  /* Back */
  .card-back {
    left: 276px; top: 608px; width: 618px; height: 374px;
    background: radial-gradient(circle at 40% 40%, #ededee 0%, var(--paper) 60%, #d6d7d9 100%);
    color: var(--ink);
  }
  .person { position: absolute; left: 45px; top: 40px; }
  .person-name { font-size: 23px; font-weight: 700; }
  .person-role { font-size: 16px; margin-top: 2px; }
  .contact-list {
    position: absolute; left: 45px; top: 200px;
    list-style: none; font-size: 16px;
  }
  .contact-list li { display: flex; align-items: center; height: 26px; }
  .contact-list svg { width: 14px; height: 14px; margin: 0 18px 0 0; fill: var(--ink); }
  .address {
    position: absolute; left: 45px; top: 282px;
    font-size: 16px; line-height: 26px;
  }
  .back-brand {
    position: absolute; right: 46px; bottom: 58px;
    display: flex; align-items: center; gap: 12px;
  }
  .back-brand .mark { width: 26px; height: 26px; background: var(--ink); }
  .back-brand .name { font-size: 34px; font-weight: 700; letter-spacing: 1px; color: var(--ink); }
</style>
</head>
<body>
  <section class="card card-front">
    <svg class="stripes" viewBox="0 0 623 377" preserveAspectRatio="none" aria-hidden="true">
      <polygon points="60,0 160,0 420,377 320,377" fill="rgba(255,255,255,0.05)"/>
      <polygon points="240,0 330,0 590,377 500,377" fill="rgba(255,255,255,0.04)"/>
      <polygon points="560,0 623,0 623,120" fill="rgba(255,255,255,0.06)"/>
    </svg>
    <div class="brand-name">K T Masonry</div>
    <div class="intro-pill">We are a building materials supplier of</div>
    <div class="product-band">
      Ready Mixed Concrete, Bricks and Blocks, Quarry Products<br>
      Quarry Products:- Gravel, Aggregates, Sand Etc.
    </div>
    <div class="product-more">
      Cement Distributor/Retailer of Reputable Brands.<br>
      Other Concrete Products Culverts, Wave Breakers, Concrete Retaining Blocks
    </div>
  </section>

  <section class="card card-back">
    <div class="person">
      <div class="person-name">Daniel Harper</div>
      <div class="person-role">Managing Director</div>
    </div>
    <ul class="contact-list">
      <li><svg viewBox="0 0 16 16"><path d="M2 6c0-3 3-4 6-4s6 1 6 4h-3V5H5v1zM4 8h8l2 6H2z"/></svg>000 0000 0000</li>
      <li><svg viewBox="0 0 16 16"><path d="M1 3h14v10H1zM2 4.5v.5l6 4 6-4v-.5z" fill-rule="evenodd"/></svg>daniel@ktmasonry.com</li>
      <li><svg viewBox="0 0 16 16"><circle cx="8" cy="8" r="7"/><path d="M1 8h14M8 1v14M3 4h10M3 12h10" stroke="#e3e4e5" stroke-width="1" fill="none"/></svg>www.ktmasonry.com</li>
    </ul>
    <div class="address">
      234 Anywhere St., Any City,<br>
      Any Town, US 123456
    </div>
    <div class="back-brand">
      <span class="mark"></span>
      <span class="name">K T Masonry</span>
    </div>
  </section>
</body>
</html>
```